"Copper Lantern" Play - Poster Design for Theatre Group

We are an amateur theatre group based in Geneva, Switzerland. We take pride in eye-catching posters for our shows, which are printed in various sizes.
This design will be for a play in March 2016. The play is called "Copper Lantern", and it's a Marwick Medal winner from Martin Crowe-Fenwick. The play is about a couple who have everything a family could want, until they lose a child in a life-shattering accident that turns their world upside down. The play charts the couple's bittersweet search to find each other and to find comfort.
Most importantly, we want a design that will make people want to see the show. We don't want to give away the plot or be too heavy-handed about death, but we want it to be clear that it's not a comedy (although there are some lighter moments!).
Attached you will find a template for the poster. This simply has our group name and logo in the top right corner: (Lakeside Stage Players Guild presents).
You may change the color of both the text and the logo, but please do not change the font, size, or location.
Here is the information that needs to be on the poster, wherever you see fit:
play title: Copper Lantern
author byline: by Martin Crowe-Fenwick
director line: directed by Ned Pilbury
tagline: How do you keep it together when your whole world's fallen apart?
dates and times:
1-5 March 2016
(Tue-Fri 20:00, Sat 19:00)
location:
Théâtre du Colibri
Eaux-Vives, Geneva
websites:
www.lspg.ch
www.scenesansfrontiere.ch
Technical Details:
Any font or combination of fonts is acceptable. The largest text should be the play title. The author's name must be at least 50% of the title font size.
For this competition, we would like the version with A3 proportions, which will also be used at F4 (89.5 x 128 cm) and A5 sizes (14.8 x 21 cm). Therefore no text should be below 9pt at A5.
However, from the winning designer we will also need repurposed sizes of the same design. Here is a comprehensive list of the sizes we will need.
1) A3 print poster. Artwork should be 300dpi, CMYK, sent with a 1mm bleed all round, to specification PDF/X-1A:2001. We will need this image in PDF format in addition to the default Artmarketo formats.
2) Chatterbook advert picture. 1200px by 628px, RGB jpeg. This must comply with Chatterbook’s restrictions on amount of text, which is no more than 20% of area taken up by text.(https://www.chatterbook-example.com/ads/tools/text_overlay).
Because of these restrictions it is sufficient to include just the title and the author's name in this version.
3) Chatterbook cover picture: 851px by 314px. RGB jpeg. It is sufficient to include just the title and the author's name in this version.
4) Web banner. 1000px by 300px. RGB jpeg. This version should include just the main image(s), no text.

```html
<!DOCTYPE html>
<html lang="en">
<head>
<meta charset="utf-8">
<title>Copper Lantern – Lakeside Stage Players Guild</title>
<link rel="stylesheet" href="https://fonts.googleapis.com/css2?family=Raleway:ital,wght@0,200;0,300;0,700;1,300&display=swap">
<style>
  :root {
    --paper: #ffffff;
    --night: #050505;
    --ink: #e9e9e9;
    --gold: #c7b27a;
    --toy-warm: #6e5535;
    --toy-cool: #2a3436;
  }
  * { margin: 0; padding: 0; box-sizing: border-box; }
  html, body {
    width: 865px; height: 1200px; overflow: hidden;
    background: var(--paper);
  }
  .poster {
    position: relative;
    width: 865px; height: 1200px;
    background: var(--paper);
    font-family: "Raleway", sans-serif;
    color: var(--ink);
  }
  .stage {
    position: absolute;
    left: 28px; top: 28px; width: 809px; height: 1142px;
    background: var(--night);
    overflow: hidden;
  }
  .toy-photo {
    position: absolute;
    left: 12px; top: 330px; width: 790px; height: 790px;
    background:
      radial-gradient(ellipse 34% 40% at 50% 42%, var(--toy-warm) 0%, rgba(110,85,53,0.55) 45%, transparent 75%),
      radial-gradient(ellipse 22% 30% at 20% 75%, rgba(150,110,70,0.7) 0%, transparent 75%),
      radial-gradient(ellipse 26% 38% at 74% 70%, var(--toy-cool) 0%, rgba(42,52,54,0.5) 50%, transparent 80%);
  }
  .presenter {
    position: absolute;
    right: 27px; top: 10px;
    display: flex; align-items: center; gap: 16px;
  }
  .presenter-name {
    font-weight: 700; font-size: 19px; line-height: 27px;
    color: var(--gold); text-align: right;
  }
  .title {
    position: absolute;
    left: 0; right: 0; top: 172px;
    text-align: center;
    font-weight: 200; font-size: 86px; letter-spacing: 4px;
    line-height: 1; text-transform: uppercase;
    white-space: nowrap;
  }
  .credits {
    position: absolute; left: 0; right: 0; top: 262px;
    text-align: center; font-style: italic; font-weight: 300;
  }
  .byline { font-size: 22px; line-height: 30px; }
  .director { font-size: 17px; line-height: 22px; }
  .details {
    position: absolute; left: 0; right: 0; top: 885px;
    text-align: center; font-weight: 300;
    text-shadow: 0 0 8px rgba(0,0,0,0.6);
  }
  .dates { font-size: 33px; line-height: 40px; letter-spacing: 0.5px; }
  .times { font-size: 21px; line-height: 28px; }
  .venue { font-size: 36px; line-height: 44px; margin-top: 8px; }
  .district { font-size: 30px; line-height: 36px; }
  .websites {
    position: absolute; left: 0; right: 0; top: 1080px;
    text-align: center; font-style: italic; font-weight: 300;
    font-size: 17px; line-height: 25px;
  }
</style>
</head>
<body>
  <main class="poster">
    <section class="stage">
      <div class="toy-photo" role="img" aria-label="Photograph of three worn vintage stuffed toys, a large bear in striped overalls, a small bear in green dungarees and a dark grey rabbit, against black"></div>

      <header class="presenter">
        <p class="presenter-name">Lakeside Stage<br>Players Guild<br>presents</p>
        <svg width="100" height="100" viewBox="0 0 100 100" aria-hidden="true">
          <circle cx="50" cy="50" r="46" fill="none" stroke="var(--gold)" stroke-width="5"/>
        </svg>
      </header>

      <h1 class="title">Copper Lantern</h1>

      <div class="credits">
        <p class="byline">by Martin Crowe-Fenwick</p>
        <p class="director">directed by Ned Pilbury</p>
      </div>

      <div class="details">
        <p class="dates">1st to 5th MARCH 2016</p>
        <p class="times">Tue-Fri 20:00, Sat 19:00</p>
        <p class="venue">Théâtre du Colibri</p>
        <p class="district">Eaux-Vives, Geneva</p>
      </div>

      <footer class="websites">
        <p>www.lspg.ch</p>
        <p>www.scenesansfrontiere.ch</p>
      </footer>
    </section>
  </main>
</body>
</html>
```